Need Website Design for Non-Profit Veteran Site

I am looking for a very talented creative website designer for a modern feel. I'll give a little bit of guidance around what I am looking for and then your creative juices should kick in and design away. I have already purchased the domain but will need hosting (at least temporarily) and the creative design work done.The website domain is militarydocs.orgI am looking to attract current and veteran military providers (doctors, nurse practitioners, physician assistants, etc) to join and signup for membership. They would pay a yearly fee to join. Would need membership categories $135 for Provider, $55 Student, $100 for Retired, and Organization (Organization would be broken down into Less than 100 ($200), 100-249 ($250), 250-499 ($300), 500-999 ($400), 1,000-2,999 ($500), and 3,000 ($700). Would need Benefit built out and would need to accept money through CoinVane and other means. Since it's a new organization just starting, would also need a Donate button to get people to donate if they want any amount they would like. The second part of the website is that once they join, they will have acess to a list of all other providers who have registered within the website (not exportable) so they can connect with one another. If they want to see contact information this will be included in their fee as a benefit to socialize with one another. As part of the website, there will be another Veteran's portal so veterans who would like to connect with a provider around a particular speciality can reach out and request help from the doctor writing a nexus letter or letter to support the veteran who is filing a claim with the BQ. Veterans would pay a yearly sign-up fee of $30.00 and would need their membership benefits displayed. They would have access to a list of veterans in their region by state and distance, and can reach out to doctors to get their help. If a doctor and veteran agree, sharable inforamtion of medical hipaa documents can be exchanged via the website. The physician and veteran can negotiate a fee through the website only and share their details. This is a separate fee for this type of process between the provider and veteran. We will collect a $250 fee for admin on each of these and each project the veteran does with the provider will cost $450 (so essentially the doctor gets paid $450 and i get $250.00. This model could be changed over time as we start to test this out). A good example of 50% of what I'm looking for is something like the following website: https://www.lpkt.org/ It has some of the features but not all and my site should be more modernized to attract the veteran and military providers.

Target Market(s)

Current and retired military providers and veterans

Industry/Entity Type

Non Profit

Number of Pages Required

1 page

Requirements
Must have
• Military Design
• Modern Feel (Example templates for feel -https://quillmoth.com/free-photoshop-psd-web-design-template/)
• Donation box
• Stuff mentioned in the description)
Nice to have
• Open to feedback
Should not have
• Open to feedback

```html
<!DOCTYPE html>
<html lang="en">
<head>
<meta charset="utf-8">
<title>Harborwell</title>
<link href="https://fonts.googleapis.com/css2?family=Lato:wght@400;700;900&family=Roboto:wght@400;500;700&display=swap" rel="stylesheet">
<style>
:root{
  --camo-dark:#3c4336;
  --camo-mid:#56604b;
  --camo-light:#6b7560;
  --red:#b0123f;
  --blue:#1b5a9c;
  --footer:#134f8f;
  --white:#ffffff;
  --ink:#333333;
  --muted:#777777;
  --rule:#e3e3e3;
}
*{margin:0;padding:0;box-sizing:border-box}
html,body{width:1200px;height:2230px;overflow:hidden}
body{position:relative;font-family:'Roboto',sans-serif;color:var(--ink);
  background:linear-gradient(160deg,var(--camo-mid) 0%,var(--camo-dark) 35%,var(--camo-light) 60%,var(--camo-dark) 100%);}
.abs{position:absolute}
/* header */
.brand{left:98px;top:36px;font-family:'Lato',sans-serif;font-weight:900;font-size:30px;color:var(--white);letter-spacing:.3px}
.btn-join{left:902px;top:35px;width:90px;height:39px;background:var(--red);color:var(--white);font:700 16px 'Roboto',sans-serif;display:flex;align-items:center;justify-content:center}
.btn-signup{left:1011px;top:34px;width:90px;height:40px;border:1.5px solid var(--white);color:var(--white);font:700 16px 'Roboto',sans-serif;display:flex;align-items:center;justify-content:center}
.nav{left:0;top:106px;width:1200px;height:47px;background:var(--blue)}
.nav ul{list-style:none;display:flex;position:absolute;left:98px;top:0;height:47px}
.nav li{color:var(--white);font:500 14px 'Roboto',sans-serif;display:flex;align-items:center;height:47px;padding:0 21px}
.nav li.active{background:var(--red)}
/* hero */
.hero-photo{left:0;top:153px;width:1200px;height:571px;
  background:linear-gradient(100deg,#6d6259 0%,#9b8a7c 30%,#c9c1b6 55%,#8d8a70 75%,#5d5848 100%)}
.hero-shade{left:0;top:153px;width:620px;height:571px;background:linear-gradient(90deg,rgba(40,30,25,.45),rgba(40,30,25,0))}
.hero-title{left:96px;top:303px;font:900 54px 'Lato',sans-serif;color:var(--white)}
.hero-text{left:98px;top:392px;width:470px;font:400 19px/1.45 'Lato',sans-serif;color:var(--white)}
.btn-donate{left:98px;top:484px;width:170px;height:46px;background:var(--red);color:var(--white);font:400 20px 'Lato',sans-serif;display:flex;align-items:center;justify-content:center;letter-spacing:.4px}
/* talk about */
.section-title{left:0;width:1200px;text-align:center;top:810px;font:700 30px 'Lato',sans-serif;color:var(--white)}
.topic{top:876px;width:309px;height:144px;background:var(--white);display:flex;align-items:center;padding-left:12px}
.topic.featured{background:var(--red)}
.topic .thumb{width:125px;height:120px;border:3px solid #eee;background:linear-gradient(135deg,#dfe5ea,#a9b8c6)}
.topic.featured .thumb{background:linear-gradient(135deg,#8fb9d6,#3f7fb3)}
.topic .label{margin-left:24px;font:700 22px/1.75 'Roboto',sans-serif;color:#333}
.topic.featured .label{color:var(--white)}
/* banner */
.banner{left:98px;top:1112px;width:1004px;height:159px;background:linear-gradient(90deg,#8a8680,#a6a39d 50%,#6f6e68);display:flex;align-items:center;justify-content:center}
.banner span{font:700 28px 'Roboto',sans-serif;color:var(--white);letter-spacing:.2px}
/* columns */
.col{top:1362px;width:309px}
.col h3{font:400 22px 'Lato',sans-serif;color:var(--white);padding-bottom:16px;border-bottom:2px solid rgba(255,255,255,.55)}
.card{margin-top:32px;height:333px;background:var(--white)}
.row{height:83px;display:flex;align-items:center;border-bottom:1px solid var(--rule);padding-left:12px}
.row:last-child{border-bottom:none}
.icon{width:60px;height:60px;border-radius:50%;background:var(--footer);display:flex;align-items:center;justify-content:center;flex-shrink:0}
.pic{width:64px;height:60px;flex-shrink:0;background:linear-gradient(135deg,#c9d3dc,#7f93a6)}
.row .txt{margin-left:16px}
.row .t{font:400 14px 'Roboto',sans-serif;color:#333;text-transform:uppercase}
.row .s{font:400 11.5px 'Roboto',sans-serif;color:var(--muted);margin-top:10px}
.more{margin-top:31px;height:40px;background:var(--red);color:var(--white);font:500 15px 'Roboto',sans-serif;display:flex;align-items:center;justify-content:space-between;padding:0 16px}
.feed{padding:6px 8px}
.feed-head{display:flex;justify-content:space-between;align-items:center;font:500 13px 'Roboto',sans-serif;color:#333;padding:2px 4px 10px;border-bottom:1px solid var(--rule)}
.feed-head b{color:#1da1f2;font-weight:500}
.tweet{display:flex;padding:10px 4px 0}
.avatar{width:34px;height:34px;border-radius:50%;background:#6b8196;flex-shrink:0}
.tweet-body{margin-left:10px;font:400 11px/1.5 'Roboto',sans-serif;color:#555}
.tweet-body .who{font-size:11px;color:#555}
.tweet-body .who i{color:#1da1f2;font-style:normal}
.tweet-body p{margin-top:10px}
.tweet-body .tag{color:#1da1f2}
.tweet-img{margin-top:8px;width:240px;height:150px;background:linear-gradient(135deg,#c8d3dc,#7c8c98 60%,#9a7a63)}
.stats{display:flex;gap:30px;font:400 10px 'Roboto',sans-serif;color:#1da1f2;margin-top:8px;padding-left:0}
/* footer */
.footer{left:0;top:1933px;width:1200px;height:297px;background:var(--footer)}
.f-head{top:2002px;font:700 15px 'Lato',sans-serif;color:var(--white)}
.f-links{left:102px;top:2042px;list-style:none;color:var(--white);font:400 13px 'Roboto',sans-serif}
.f-links li{margin-bottom:13px}
.f-links li::before{content:"»";margin-right:9px}
.f-contact{left:317px;top:2046px;color:var(--white);font:400 13px 'Roboto',sans-serif}
.f-contact div{display:flex;align-items:center;gap:16px;margin-bottom:18px}
.news{left:597px;top:2048px;width:255px;height:34px;border-radius:17px;background:var(--white);display:flex;align-items:center;justify-content:space-between;padding:0 4px 0 16px}
.news span{font:400 12px 'Roboto',sans-serif;color:#999}
.news b{background:var(--red);color:var(--white);font:500 12px 'Roboto',sans-serif;border-radius:14px;padding:6px 17px}
.social{left:951px;top:2048px;display:flex;gap:8px}
.social span{width:33px;height:33px;border-radius:50%;background:var(--white)}
.f-rule{left:98px;top:2151px;width:1004px;height:1px;background:rgba(255,255,255,.45)}
.copy{left:0;width:1200px;top:2178px;text-align:center;font:400 12px 'Roboto',sans-serif;color:var(--white)}
</style>
</head>
<body>

<header>
  <div class="abs brand">HARBORWELL</div>
  <div class="abs btn-join">JOIN</div>
  <div class="abs btn-signup">SIGNUP</div>
</header>

<nav class="abs nav">
  <ul>
    <li class="active">HOME</li><li>ABOUT US</li><li>MEMBERSHIP</li><li>EDUCATION</li><li>RESEARCH</li><li>CONFERENCES</li><li>PUBLICATIONS</li><li>CONTACT US</li>
  </ul>
</nav>

<section class="hero">
  <div class="abs hero-photo" role="img" aria-label="Photo of a smiling military family in front of a house with an American flag"></div>
  <div class="abs hero-shade"></div>
  <h1 class="abs hero-title">HARBORWELL</h1>
  <p class="abs hero-text">At vero eos et accusamus et iusto odio dignissimos ducimus qui blanditiis praesentium voluptatum</p>
  <div class="abs btn-donate">DONATE</div>
</section>

<section>
  <h2 class="abs section-title">WE TALK ABOUT</h2>
  <div class="abs topic" style="left:98px"><div class="thumb" role="img" aria-label="Photo of two doctors"></div><div class="label">Good<br>Doctors</div></div>
  <div class="abs topic featured" style="left:446px"><div class="thumb" role="img" aria-label="Photo of two nurse practitioners in scrubs"></div><div class="label">Nurse<br>Practitioners</div></div>
  <div class="abs topic" style="left:793px"><div class="thumb" role="img" aria-label="Photo of a team of physician assistants"></div><div class="label">Physician<br>Assistants</div></div>
</section>

<div class="abs banner" role="img" aria-label="Photo of a stethoscope on medical paperwork"><span>VETERANS WOULD PAY A YEARLY SIGN-UP FEE OF $30.00</span></div>

<section class="abs col" style="left:98px">
  <h3>BENEFITS</h3>
  <div class="card">
    <div class="row"><div class="icon"><svg width="30" height="30" viewBox="0 0 30 30"><rect x="3" y="8" width="24" height="18" rx="2" fill="#fff"/><rect x="11" y="4" width="8" height="5" fill="none" stroke="#fff" stroke-width="2"/><path d="M15 11v12M9 17h12" stroke="#134f8f" stroke-width="3"/></svg></div><div class="txt"><div class="t">Active Duty</div><div class="s">At vero eos et accusamus et iusto</div></div></div>
    <div class="row"><div class="icon"><svg width="32" height="30" viewBox="0 0 32 30"><path d="M16 27 4 15a7 7 0 0 1 12-9 7 7 0 0 1 12 9z" fill="none" stroke="#fff" stroke-width="2.4"/><path d="M5 15h6l2-4 3 8 2-4h9" fill="none" stroke="#fff" stroke-width="2"/></svg></div><div class="txt"><div class="t">Health Care</div><div class="s">At vero eos et accusamus et iusto</div></div></div>
    <div class="row"><div class="icon"><svg width="32" height="30" viewBox="0 0 32 30"><circle cx="10" cy="9" r="4" fill="#fff"/><circle cx="22" cy="9" r="4" fill="#fff"/><path d="M3 26c0-7 3-11 7-11s7 4 7 11zM15 26c0-7 3-11 7-11s7 4 7 11z" fill="#fff"/></svg></div><div class="txt"><div class="t">Military Spouse &amp; Family</div><div class="s">At vero eos et accusamus et iusto</div></div></div>
    <div class="row"><div class="icon"><svg width="30" height="30" viewBox="0 0 30 30"><path d="M7 9h16l-2-5H9z" fill="#fff"/><circle cx="15" cy="13" r="4.5" fill="#fff"/><path d="M5 28c0-7 4-10 10-10s10 3 10 10z" fill="#fff"/></svg></div><div class="txt"><div class="t">Reserve &amp; Guard</div><div class="s">At vero eos et accusamus et iusto</div></div></div>
  </div>
  <div class="more">SEE ALL BENEFITS DETAILS <svg width="16" height="16" viewBox="0 0 16 16"><circle cx="8" cy="8" r="8" fill="#fff"/><path d="M6 4l4 4-4 4" fill="none" stroke="#b0123f" stroke-width="2"/></svg></div>
</section>

<section class="abs col" style="left:446px">
  <h3>LATEST NEWS</h3>
  <div class="card">
    <div class="row"><div class="pic" role="img" aria-label="Photo of a soldier"></div><div class="txt"><div class="t">Tenetur Sapiente</div><div class="s">At vero eos et accusamus et iusto</div></div></div>
    <div class="row"><div class="pic" role="img" aria-label="Photo of a doctor at a desk"></div><div class="txt"><div class="t">Power of Choice</div><div class="s">At vero eos et accusamus et iusto</div></div></div>
    <div class="row"><div class="pic" role="img" aria-label="Photo of a veteran seated"></div><div class="txt"><div class="t">Active Club</div><div class="s">At vero eos et accusamus et iusto</div></div></div>
    <div class="row"><div class="pic" role="img" aria-label="Photo of medical staff in scrubs"></div><div class="txt"><div class="t">Rejects Pleasures</div><div class="s">At vero eos et accusamus et iusto</div></div></div>
  </div>
  <div class="more">SEE ALL NEWS INFORMATION <svg width="16" height="16" viewBox="0 0 16 16"><circle cx="8" cy="8" r="8" fill="#fff"/><path d="M6 4l4 4-4 4" fill="none" stroke="#b0123f" stroke-width="2"/></svg></div>
</section>

<section class="abs col" style="left:793px">
  <h3>TALK TO US</h3>
  <div class="card feed">
    <div class="feed-head"><span>Tweets by <b>@harborwellnet</b></span><svg width="16" height="16"><circle cx="8" cy="8" r="7" fill="#1da1f2"/></svg></div>
    <div class="tweet">
      <div class="avatar"></div>
      <div class="tweet-body">
        <div class="who">Our Power Of Choice <i>@harborwellnet.38m</i><br>Homecoming Complete.</div>
        <p>At vero eoset accusamus et etiusto vero odio dignissimos ducimus qui blanditiis prae sentium voluptatum deleniti <span class="tag">#tagjhmsv</span></p>
        <div class="tweet-img" role="img" aria-label="Photo of a doctor talking with a patient"></div>
        <div class="stats"><span>9</span><span>18</span><span>188</span></div>
      </div>
    </div>
  </div>
  <div class="more">TWEET US <svg width="14" height="14"><circle cx="7" cy="7" r="6" fill="#fff"/></svg></div>
</section>

<footer>
  <div class="abs footer"></div>
  <div class="abs f-head" style="left:102px">QUICK LINKS</div>
  <ul class="abs f-links"><li>Home</li><li>About Us</li><li>MemberShip</li></ul>
  <div class="abs f-head" style="left:317px">CONTACT US</div>
  <div class="abs f-contact">
    <div><svg width="15" height="15" viewBox="0 0 16 16"><path d="M3 1l3 1 1 4-2 1a9 9 0 0 0 4 4l1-2 4 1 1 3-2 2C7 15 1 9 1 3z" fill="#fff"/></svg>(+1) 123 456 7890</div>
    <div><svg width="15" height="12" viewBox="0 0 16 12"><rect width="16" height="12" fill="#fff"/><path d="M0 0l8 6 8-6" fill="none" stroke="#134f8f" stroke-width="1.5"/></svg>info@harborwellnet.com</div>
  </div>
  <div class="abs f-head" style="left:597px">NEWSLETTER SIGN UP</div>
  <div class="abs news"><span>Email address</span><b>Subscribe</b></div>
  <div class="abs f-head" style="left:951px">FOLLOW US</div>
  <div class="abs social"><span></span><span></span><span></span><span></span></div>
  <div class="abs f-rule"></div>
  <div class="abs copy">© Copyright 2018 Harborwell. All Rights Reserved &nbsp;&nbsp; | &nbsp;&nbsp; Terms &amp; Conditions.</div>
</footer>

</body>
</html>
```